Business Card & Letterhead Design

We a financial advice company based in Australia. We provide advice to wealthy farmers.

We are changing our business name FROM Brightvale Financial TO Tallowmere Wealth and we need a new letterhead and double sided business card design

Attached is designs from our previous branding (Brightvale Financial) as it includes all the details we require on the new Tallowmere Wealth business cards and letterhead.

Need extra days to review

```html
<!DOCTYPE html>
<html lang="en">
<head>
<meta charset="utf-8">
<title>Tallowmere Wealth – Stationery</title>
<link href="https://fonts.googleapis.com/css2?family=Marcellus&family=PT+Serif:wght@700&family=Roboto:wght@400&display=swap" rel="stylesheet">
<style>
  :root{
    --backdrop:#9b9b9b;
    --paper:#f7f7f5;
    --ink:#3d3d3d;
    --ink-soft:#555;
    --card-dark:#3e3e3e;
    --divider:#7a7a7a;
    --faint:#ececea;
    --white:#ffffff;
  }
  *{margin:0;padding:0;box-sizing:border-box}
  html,body{width:1200px;height:1032px;overflow:hidden}
  body{background:var(--backdrop);position:relative;font-family:'Roboto',sans-serif}
  .sheet{position:absolute}
  .abs{position:absolute}
  .wordmark{font-family:'Marcellus',serif;letter-spacing:.02em;white-space:nowrap;text-transform:uppercase;text-align:center}
  .tagline{font-family:'Roboto',sans-serif;text-transform:uppercase;white-space:nowrap;text-align:center}
  .ring{position:absolute;border-radius:50%}

  /* Letterhead */
  .letterhead{left:446px;top:74px;width:626px;height:884px;background:var(--paper);overflow:hidden}
  .letterhead .ring.logo{left:126px;top:46px;width:68px;height:68px;border:2.5px solid var(--ink)}
  .letterhead .wordmark{left:60px;width:200px;top:118px;font-size:18px;color:var(--ink)}
  .letterhead .tagline{left:60px;width:200px;top:137px;font-size:7.6px;letter-spacing:.22em;color:var(--ink-soft)}
  .contact-list{position:absolute;right:51px;list-style:none;text-align:right;color:var(--ink);font-size:10px}
  .contact-list li{height:14.5px;line-height:14.5px;display:flex;justify-content:flex-end;align-items:center;gap:7px}
  .contact-list svg{width:9px;height:9px;fill:var(--ink)}
  .contact-list.top{top:46px}
  .contact-list.addr{top:133px}
  .header-rule{position:absolute;left:0;top:0;width:626px;height:250px}
  .watermark-ring{left:116px;top:344px;width:396px;height:396px;border:8px solid var(--faint)}

  /* Card front */
  .card{width:271px;height:163px;overflow:hidden}
  .card-front{left:127px;top:330px;background:var(--card-dark)}
  .card-front .deco{left:133px;top:14px;width:150px;height:150px;border:5px solid #4a4a4a}
  .card-front .ring.logo{left:114px;top:49px;width:42px;height:42px;border:2px solid var(--white)}
  .card-front .wordmark{left:0;width:271px;top:99px;font-size:14px;color:var(--white)}
  .card-front .tagline{left:0;width:271px;top:117px;font-size:6px;letter-spacing:.24em;color:#d8d8d8}

  /* Card back */
  .card-back{left:127px;top:537px;background:var(--card-dark)}
  .card-back .shape{position:absolute;left:0;top:0;width:271px;height:163px}
  .card-back .ring.logo{left:183px;top:49px;width:38px;height:38px;border:2px solid var(--ink)}
  .card-back .wordmark{left:136px;width:132px;top:96px;font-size:11.5px;color:var(--ink)}
  .card-back .tagline{left:136px;width:132px;top:110px;font-size:4.6px;letter-spacing:.2em;color:var(--ink-soft)}
  .person{position:absolute;left:12px;top:12px;color:var(--white)}
  .person-name{font-family:'PT Serif',serif;font-weight:700;font-size:9.5px;letter-spacing:.02em;text-transform:uppercase}
  .person-role{font-size:5.6px;line-height:7.5px;color:#e6e6e6;margin-top:2px}
  .card-contacts{position:absolute;left:13px;top:68px;list-style:none;color:#eaeaea;font-size:5.8px}
  .card-contacts li{display:flex;gap:6px;line-height:9.2px}
  .card-contacts svg{width:5.5px;height:5.5px;fill:#eaeaea;margin-top:1.8px;flex:none}
</style>
</head>
<body>
<svg width="0" height="0" style="position:absolute" aria-hidden="true">
  <defs>
    <symbol id="i-phone" viewBox="0 0 10 10"><path d="M1 3c0-2 8-2 8 0v1H7V3H3v1H1z M2 5h6l1 4H1z"/></symbol>
    <symbol id="i-mobile" viewBox="0 0 10 10"><path d="M2.5 0h5v10h-5z M3.5 1v7h3V1z"/></symbol>
    <symbol id="i-print" viewBox="0 0 10 10"><path d="M3 0h4v3H3z M0 3h10v5H8V6H2v2H0z M2.5 7h5v3h-5z"/></symbol>
    <symbol id="i-mail" viewBox="0 0 10 10"><path d="M0 2h10v6H0z" opacity=".9"/><path d="M0 2l5 3.5L10 2" stroke="#fff" stroke-width=".8" fill="none"/></symbol>
    <symbol id="i-web" viewBox="0 0 10 10"><circle cx="5" cy="5" r="4.5"/><path d="M.5 5h9M5 .5v9" stroke="#fff" stroke-width=".6"/></symbol>
    <symbol id="i-pin" viewBox="0 0 10 10"><path d="M5 0a3.5 3.5 0 0 1 3.5 3.5C8.5 6 5 10 5 10S1.5 6 1.5 3.5A3.5 3.5 0 0 1 5 0z M5 2a1.4 1.4 0 1 0 0 2.8A1.4 1.4 0 0 0 5 2z" fill-rule="evenodd"/></symbol>
  </defs>
</svg>

<section class="sheet letterhead" aria-label="Letterhead">
  <svg class="header-rule" viewBox="0 0 626 250" aria-hidden="true">
    <polyline points="48,158 284,158 328,126 580,126" fill="none" stroke="#3d3d3d" stroke-width="1.6"/>
  </svg>
  <div class="ring logo"></div>
  <div class="abs wordmark">Tallowmere Wealth</div>
  <div class="abs tagline">Strategic Financial Advice</div>
  <ul class="contact-list top">
    <li>(07) 3000 1234 <svg><use href="#i-phone"/></svg></li>
    <li>(07) 3000 5678 <svg><use href="#i-mobile"/></svg></li>
    <li>0400 123 456 <svg><use href="#i-print"/></svg></li>
    <li>sam@brightvalefinancial.com.au <svg><use href="#i-mail"/></svg></li>
    <li>www.brightvalefinancial.com.au <svg><use href="#i-web"/></svg></li>
  </ul>
  <ul class="contact-list addr">
    <li>PO Box 1200 Easton QLD 4000 <svg><use href="#i-pin"/></svg></li>
    <li>Suite 4A, 18 Harlow St Riverbend QLD 4000 <svg><use href="#i-pin"/></svg></li>
  </ul>
  <div class="ring watermark-ring"></div>
</section>

<section class="sheet card card-front" aria-label="Business card front">
  <div class="ring deco"></div>
  <div class="ring logo"></div>
  <div class="abs wordmark">Tallowmere Wealth</div>
  <div class="abs tagline">Strategic Financial Advice</div>
</section>

<section class="sheet card card-back" aria-label="Business card back">
  <svg class="shape" viewBox="0 0 271 163" aria-hidden="true">
    <path d="M145 0 Q118 82 149 163 L271 163 L271 0 Z" fill="#7a7a7a"/>
    <path d="M150 0 Q124 82 154 163 L271 163 L271 0 Z" fill="#f7f7f5"/>
  </svg>
  <div class="person">
    <div class="person-name">Sam Doyle</div>
    <div class="person-role">B.Ag.Ec. Dip F.P. CFP®<br>Managing Director</div>
  </div>
  <ul class="card-contacts">
    <li><svg><use href="#i-phone"/></svg>(07) 3000 1234</li>
    <li><svg><use href="#i-mobile"/></svg>(07) 3000 5678</li>
    <li><svg><use href="#i-print"/></svg>0400 123 456</li>
    <li><svg><use href="#i-mail"/></svg>sam@brightvalefinancial.com.au</li>
    <li><svg><use href="#i-web"/></svg>www.brightvalefinancial.com.au</li>
    <li><svg><use href="#i-pin"/></svg>Suite 4A, 18 Harlow St<br>Riverbend QLD 4000</li>
    <li><svg><use href="#i-pin"/></svg>PO Box 1200<br>Easton QLD 4000</li>
  </ul>
  <div class="ring logo"></div>
  <div class="abs wordmark">Tallowmere Wealth</div>
  <div class="abs tagline">Strategic Financial Advice</div>
</section>
</body>
</html>
```